Quillmarsh Property Solutions need a business card design

Hello guys. We would need a business card design asap please.
We are a start up property investment business based in London UK specialised in buying, selling, managing and letting properties and helping distressed property owners.
The name of our Business is Quillmarsh, the logo symbolises the four fundamental elements of the world (earth, air, fire and water) and so it stands for strength, stability, longevity.
We would like the business card to communicate professionalism and reliability. Many many thanks indeed for your work.

Details:

1.) Rosalind Updike
Property Investor
Mobile: +44(0)7700123456
Email: rosalind.quillmarsh@mailbox-example.com

2.) Dominic Updike
Property Investor
Mobile: +44(0)7700987654
Email: dominic.quillmarsh@mailbox-example.com

```html
<!DOCTYPE html>
<html lang="en">
<head>
<meta charset="utf-8">
<title>Quillmarsh Property Solutions – Business Card</title>
<link rel="stylesheet" href="https://fonts.googleapis.com/css2?family=Open+Sans:wght@400;600;700&display=swap">
<style>
  :root {
    --canvas: #e9e9ee;
    --card-white: #ffffff;
    --green: #08b04a;
    --green-dark: #019a3c;
    --green-light: #18b555;
    --name-blue: #1a56c4;
    --text-grey: #5e5e5e;
    --brand-grey: #8a8a8a;
    --white: #ffffff;
  }
  * { margin: 0; padding: 0; box-sizing: border-box; }
  html, body {
    width: 1200px; height: 987px; overflow: hidden;
    background: var(--canvas);
    font-family: "Open Sans", Arial, sans-serif;
  }
  .canvas {
    width: 1200px; height: 987px;
    display: flex; flex-direction: column; align-items: center; justify-content: center;
    gap: 40px;
  }
  .card {
    position: relative;
    width: 760px; height: 434px;
    border-radius: 34px;
    overflow: hidden;
    box-shadow: 0 6px 18px rgba(0,0,0,0.12);
  }
  /* Front */
  .card-front { background: var(--card-white); }
  .card-front .wave { position: absolute; inset: 0; display: block; }
  .wave-fill { fill: var(--green); }
  .wave-swoosh { fill: none; stroke: var(--white); stroke-width: 5; stroke-linecap: round; }
  .brand {
    position: absolute; left: 120px; top: 96px;
    display: flex; align-items: center; gap: 16px;
  }
  .brand-mark { width: 26px; height: 26px; background: var(--brand-grey); }
  .brand-name {
    font-weight: 700; font-size: 26px; letter-spacing: 1px;
    color: var(--brand-grey); text-transform: uppercase; line-height: 1.15;
  }
  .holder { position: absolute; right: 52px; top: 200px; text-align: right; }
  .holder-name { font-weight: 600; font-size: 30px; color: var(--name-blue); letter-spacing: 0.5px; }
  .holder-role { font-size: 22px; color: var(--text-grey); margin-top: 2px; }
  .contact {
    position: absolute; list-style: none;
    color: var(--white); font-size: 20px; white-space: nowrap;
  }
  .contact-phone { top: 346px; left: 150px; }
  .contact-email { top: 386px; left: 50px; }
  .contact li { display: flex; align-items: center; gap: 10px; }
  .contact svg { width: 20px; height: 20px; flex: none; }
  /* Back */
  .card-back {
    background: radial-gradient(ellipse at 40% 30%, var(--green-light), var(--green-dark) 80%);
    display: flex; flex-direction: column; align-items: center; justify-content: center;
    gap: 26px;
  }
  .back-brand { display: flex; align-items: center; gap: 18px; }
  .back-mark { width: 40px; height: 40px; border-radius: 50%; background: var(--white); }
  .back-name {
    font-weight: 700; font-size: 44px; color: var(--white);
    text-transform: uppercase; letter-spacing: 2px;
  }
  .back-url { font-size: 24px; color: var(--white); letter-spacing: 3px; }
</style>
</head>
<body>
<main class="canvas">
  <section class="card card-front" aria-label="Business card front">
    <svg class="wave" width="760" height="434" viewBox="0 0 760 434" aria-hidden="true">
      <path class="wave-fill" d="M0 130 C 50 280, 280 290, 500 325 C 640 348, 720 375, 760 400 L 760 434 L 0 434 Z"/>
      <path class="wave-swoosh" d="M24 226 C 90 330, 320 322, 520 352 C 640 372, 710 400, 745 434"/>
    </svg>

    <div class="brand">
      <span class="brand-mark"></span>
      <span class="brand-name">Quillmarsh<br>Property Solutions</span>
    </div>

    <div class="holder">
      <p class="holder-name">Rosalind Updike</p>
      <p class="holder-role">Property Investor</p>
    </div>

    <ul class="contact contact-phone">
      <li>
        <svg viewBox="0 0 20 20"><rect x="5" y="1" width="10" height="18" rx="2" fill="none" stroke="#fff" stroke-width="2"/><rect x="7" y="4" width="6" height="6" fill="#fff"/><circle cx="10" cy="15" r="1.5" fill="#fff"/></svg>
        +44(0)7700123456
      </li>
    </ul>
    <ul class="contact contact-email">
      <li>
        <svg viewBox="0 0 20 20"><rect x="1" y="4" width="18" height="12" rx="1" fill="none" stroke="#fff" stroke-width="2"/><path d="M1 5 L10 11 L19 5" fill="none" stroke="#fff" stroke-width="2"/></svg>
        rosalind.quillmarsh@mailbox-example.com
      </li>
    </ul>
  </section>

  <section class="card card-back" aria-label="Business card back">
    <div class="back-brand">
      <span class="back-mark"></span>
      <span class="back-name">Quillmarsh</span>
    </div>
    <p class="back-url">www.quillmarsh-example.com</p>
  </section>
</main>
</body>
</html>
```